Gift Cards in the Mail Envelope

Mailing out gift cards in the envelope. Need an eye popping envelope. Please look at the enclosed images. The envelope should look like that.

Low design quality

```html
<!DOCTYPE html>
<html lang="en">
<head>
<meta charset="UTF-8">
<title>Gift Card Envelope</title>
<link href="https://fonts.googleapis.com/css2?family=Lato:wght@400&family=Pinyon+Script&display=swap" rel="stylesheet">
<style>
  :root {
    --backdrop: #e4e4e4;
    --paper: #ffffff;
    --gold: #be850a;
    --gold-script: #c9a03a;
    --rule: #9a9a9a;
    --ink: #222222;
  }
  html, body {
    margin: 0;
    padding: 0;
    overflow: hidden;
  }
  body {
    width: 1200px;
    height: 1200px;
    background: var(--backdrop);
    position: relative;
    font-family: "Lato", sans-serif;
  }
  .envelope {
    position: absolute;
    background: var(--paper);
    box-shadow: 0 2px 4px rgba(0, 0, 0, 0.35);
  }
  .envelope-front {
    left: 190px;
    top: 192px;
    width: 818px;
    height: 408px;
  }
  .recipient-lines {
    position: absolute;
    left: 76px;
    top: 60px;
    width: 340px;
  }
  .recipient-line {
    height: 0;
    border-top: 1.5px solid var(--rule);
    margin-bottom: 46px;
  }
  .return-address {
    position: absolute;
    left: 76px;
    top: 360px;
    margin: 0;
    font-size: 15px;
    color: var(--ink);
    white-space: nowrap;
  }
  .greeting {
    position: absolute;
    left: 560px;
    top: 190px;
    width: 220px;
    font-family: "Pinyon Script", cursive;
    color: var(--gold-script);
    line-height: 1;
  }
  .greeting-main {
    display: block;
    font-size: 104px;
    padding-left: 22px;
  }
  .greeting-sub {
    display: block;
    font-size: 52px;
    margin-top: -18px;
  }
  .envelope-back {
    left: 192px;
    top: 704px;
    width: 814px;
    height: 404px;
  }
  .envelope-flap {
    position: absolute;
    left: 0;
    top: 0;
    width: 814px;
    height: 404px;
  }
</style>
</head>
<body>
  <section class="envelope envelope-front">
    <div class="recipient-lines">
      <div class="recipient-line"></div>
      <div class="recipient-line"></div>
      <div class="recipient-line"></div>
    </div>
    <p class="return-address">421, Address line goes here Country Name, 45452</p>
    <div class="greeting">
      <span class="greeting-main">Gift</span>
      <span class="greeting-sub">For You</span>
    </div>
  </section>

  <section class="envelope envelope-back">
    <svg class="envelope-flap" viewBox="0 0 814 404" aria-hidden="true">
      <path d="M6 0 H808 V40 Q808 56 792 62 L418 204 Q407 210 396 204 L22 62 Q6 56 6 40 Z" fill="var(--gold)"/>
    </svg>
  </section>
</body>
</html>
```